KRL Stationery Design Project

Dear Designers,
We need a new stationery design for company to match our new logo.
Designers should provide a design for the following:
1. Business Card: 3.5x2 Inches.
2. Letterhead: A4 size.
3. Envelops: 25x35.5 Cm.
You can keep the Arabic name at the bottom of the logo Or you can use the separate attached Arabic Name.
Please refer to the attached logo guide for design information.
Sample Business Card information:
Name: Tarek Sowan
Position: Operation Manager
Tel: +966 920007164 Ex. 500
Fax: +966 (3)8842617
Mob: +966 (5)00263817
email: tarek@krl-example.com.sa
URL: www.krl-example.com.sa
Address:
Nakheel Heights, Suite 718
Zayed bin Omar Str.
Khobar, 31847
Saudi Arabia
Updates
Dear All,
Please note, we had uploaded our logo along with Arabic writing in Adobe illustrator format (.ai).
Regards,
Karim
Dear All,
A sample data for the business card had been added as per your request.
Regards,
Karim

```html
<!DOCTYPE html>
<html lang="en">
<head>
<meta charset="utf-8">
<title>KRL Business Card</title>
<link rel="stylesheet" href="https://fonts.googleapis.com/css2?family=Open+Sans:wght@400;600;700&display=swap">
<style>
  :root {
    --navy: #062b52;
    --grey: #9a9a9a;
    --ink: #3c3c3c;
    --bg: #e6e9ec;
    --white: #ffffff;
  }
  * { margin: 0; padding: 0; box-sizing: border-box; }
  html, body { width: 1200px; height: 965px; overflow: hidden; }
  body {
    background: var(--bg);
    font-family: "Open Sans", Arial, sans-serif;
    position: relative;
  }
  .card {
    position: absolute;
    width: 646px;
    height: 369px;
    overflow: hidden;
  }
  .card-front {
    left: 277px; top: 96px;
    background: var(--navy);
  }
  .front-name {
    position: absolute;
    left: 0; right: 0; top: 150px;
    text-align: center;
    color: var(--white);
    font-weight: 700;
    font-size: 64px;
    letter-spacing: 4px;
    line-height: 1;
  }
  .front-url {
    position: absolute;
    left: 0; right: 0; top: 317px;
    text-align: center;
    color: var(--white);
    font-size: 14px;
  }
  .card-back {
    left: 277px; top: 499px;
    background: linear-gradient(110deg, var(--white) 55%, #e4e4e4 100%);
  }
  .back-name {
    position: absolute;
    left: 84px; top: 112px;
    width: 240px;
    text-align: center;
    color: var(--navy);
    font-weight: 700;
    font-size: 50px;
    letter-spacing: 3px;
    line-height: 1;
  }
  .person {
    position: absolute;
    left: 380px; top: 76px;
  }
  .person-name {
    color: var(--navy);
    font-weight: 700;
    font-size: 21px;
    line-height: 1.2;
  }
  .person-title {
    color: var(--ink);
    font-size: 15px;
    margin-top: 2px;
  }
  .divider {
    position: absolute;
    left: 380px; right: 0; top: 137px;
    height: 2px;
    background: #b9b9b9;
  }
  .address {
    position: absolute;
    left: 380px; top: 154px;
    color: var(--ink);
    font-size: 14.5px;
    line-height: 21.5px;
  }
  .contacts {
    position: absolute;
    left: 380px; top: 224px;
    list-style: none;
    color: var(--ink);
    font-size: 14.5px;
    line-height: 21.5px;
  }
  .contacts li { display: flex; align-items: center; gap: 8px; }
  .contacts svg { width: 15px; height: 15px; fill: var(--navy); flex: none; }
  .footer-band {
    position: absolute;
    left: 0; right: 0; bottom: 0;
    height: 17px;
    background: var(--navy);
  }
  .url-tab {
    position: absolute;
    left: 344px; bottom: 0;
    width: 268px; height: 37px;
  }
  .url-tab svg { position: absolute; inset: 0; }
  .url-tab span {
    position: absolute;
    left: 0; right: 0; top: 7px;
    text-align: center;
    color: var(--white);
    font-size: 14px;
  }
</style>
</head>
<body>
  <section class="card card-front">
    <div class="front-name">KRL</div>
    <div class="front-url">www.krl-example.com.sa</div>
  </section>

  <section class="card card-back">
    <div class="back-name" style="color:var(--navy)">KRL</div>

    <div class="person">
      <div class="person-name">Tarek Sowan</div>
      <div class="person-title">Operation Manager</div>
    </div>
    <div class="divider"></div>

    <address class="address" style="font-style:normal">
      Nakheel Heights, Suite 718<br>
      Zayed bin Omar Str. Khobar<br>
      31847, Saudi Arabia
    </address>

    <ul class="contacts">
      <li><svg viewBox="0 0 16 16" aria-hidden="true"><path d="M3 1l3 3-1.5 2a9 9 0 0 0 5.5 5.5L12 10l3 3-2 2C7 15 1 9 1 3z"/></svg>+966 920007164 Ex. 500</li>
      <li><svg viewBox="0 0 16 16" aria-hidden="true"><rect x="4" y="1" width="8" height="5"/><rect x="1" y="6" width="14" height="9" rx="1"/></svg>+966 (3)8842617</li>
      <li><svg viewBox="0 0 16 16" aria-hidden="true"><path d="M4 0h8a1 1 0 0 1 1 1v14a1 1 0 0 1-1 1H4a1 1 0 0 1-1-1V1a1 1 0 0 1 1-1zm1 2v10h6V2z"/></svg>+966 (5)00263817</li>
      <li><svg viewBox="0 0 16 16" aria-hidden="true"><path d="M1 3h14v10H1zm1 1v1l6 4 6-4V4z"/></svg>tarek@krl-example.com.sa</li>
    </ul>

    <div class="footer-band"></div>
    <div class="url-tab">
      <svg viewBox="0 0 268 37" width="268" height="37" aria-hidden="true">
        <path d="M0 37 C14 37 10 2 30 2 H238 C258 2 254 37 268 37 Z" fill="var(--grey)"/>
      </svg>
      <span>www.krl-example.com.sa</span>
    </div>
  </section>
</body>
</html>
```